We need letterhead, Business Cards, and envelops designed. We have attached a design of our logo and a sample of letterhead idea that was started but never perfected, it is only an idea for the letterhead if you can design something better we may love that also we are open to change.
We want a design that looks professional in style. we are a non profit trade association in the construction industry. the green color in the attached design represent green building, and we like that. also if you just want to enhance the letterhead sample that we attached that would be fine also.
Thanks and good luck
also the name that should show on the first business cards should be Morgan Feltwick, Director are web address is www.pvtrn.org

```html
<!DOCTYPE html>
<html lang="en">
<head>
<meta charset="utf-8">
<title>PVTRN Stationery</title>
<link rel="stylesheet" href="https://fonts.googleapis.com/css2?family=Montserrat:wght@400;500;600&family=Open+Sans:wght@400;600&display=swap">
<style>
  :root {
    --ink: #111111;
    --paper: #ffffff;
    --ground: #e9e9e9;
    --green: #5cb536;
    --green-dark: #3d8a24;
    --muted: #bdbdbd;
    --text: #333333;
  }
  * { box-sizing: border-box; margin: 0; padding: 0; }
  html, body { width: 1200px; height: 795px; overflow: hidden; }
  body {
    background: var(--ground);
    font-family: "Open Sans", Arial, sans-serif;
    position: relative;
  }
  .sheet {
    position: absolute;
    background: var(--paper);
    box-shadow: 0 6px 18px rgba(0,0,0,.14);
    overflow: hidden;
  }
  .brand {
    display: flex; align-items: center; gap: 6px;
    font-family: "Montserrat", Arial, sans-serif;
    font-weight: 500; color: var(--ink); letter-spacing: 2px;
  }
  .brand-mark { background: var(--green); display: block; }
  .contact-list {
    list-style: none;
    font-family: "Montserrat", Arial, sans-serif;
    color: #e6e6e6;
  }
  .contact-list li { display: flex; align-items: center; gap: 6px; }
  .contact-list .dot { width: 5px; height: 5px; background: var(--green); border-radius: 50%; flex: none; }
  .green-block { position: absolute; background: var(--green); }

  /* Business card front */
  .card-front { left: 40px; top: 60px; width: 260px; height: 149px; display: flex; align-items: center; justify-content: center; }
  .card-front .brand { font-size: 30px; }
  .card-front .brand-mark { width: 14px; height: 14px; }

  /* Business card back */
  .card-back { left: 40px; top: 230px; width: 260px; height: 149px; }
  .card-back .brand { position: absolute; left: 16px; top: 18px; font-size: 20px; }
  .card-back .brand-mark { width: 10px; height: 10px; }
  .card-back .name-strip {
    position: absolute; left: 0; bottom: 0; width: 150px; height: 62px;
    background: var(--ink); padding: 14px 16px; color: var(--paper);
    font-family: "Montserrat", Arial, sans-serif;
  }
  .card-back .person { font-size: 11px; font-weight: 600; }
  .card-back .role { font-size: 9px; color: var(--green); margin-top: 3px; }
  .card-back .contact-list { position: absolute; left: 160px; top: 60px; color: var(--text); font-size: 7.5px; line-height: 1.75; }

  /* Notebook */
  .notebook { left: 40px; top: 400px; width: 260px; height: 340px; display: flex; align-items: center; justify-content: center; }
  .notebook .spiral { position: absolute; left: 8px; top: 14px; bottom: 14px; display: flex; flex-direction: column; justify-content: space-between; }
  .notebook .spiral span { width: 8px; height: 8px; border-radius: 50%; border: 2px solid #555; display: block; }
  .notebook .brand { font-size: 30px; }
  .notebook .brand-mark { width: 14px; height: 14px; }

  /* Letterhead */
  .letterhead { left: 330px; top: 48px; width: 540px; height: 700px; }
  .letterhead .side-band { position: absolute; left: 0; top: 0; width: 130px; height: 100%; background: var(--ink); }
  .letterhead .side-band .contact-list { position: absolute; left: 16px; top: 120px; font-size: 7.5px; line-height: 1.9; }
  .letterhead .side-band .green-block { left: 0; bottom: 0; width: 130px; height: 70px; }
  .letterhead .brand { position: absolute; left: 152px; top: 34px; font-size: 30px; }
  .letterhead .brand-mark { width: 14px; height: 14px; }
  .letter { position: absolute; left: 152px; top: 110px; right: 38px; font-size: 8.5px; line-height: 1.6; color: var(--text); }
  .letter .recipient { margin-bottom: 14px; }
  .letter p { margin-bottom: 11px; }
  .letter .signature { margin-top: 18px; font-weight: 600; }

  /* Envelope */
  .envelope { left: 890px; top: 148px; width: 280px; height: 500px; }
  .envelope .brand { position: absolute; left: 24px; top: 150px; font-size: 26px; }
  .envelope .brand-mark { width: 12px; height: 12px; }
  .envelope .dark-panel { position: absolute; left: 0; bottom: 0; width: 100%; height: 250px; background: var(--ink); }
  .envelope .dark-panel .contact-list { position: absolute; left: 24px; top: 28px; font-size: 8px; line-height: 1.9; }
  .envelope .dark-panel .green-block { right: 30px; bottom: 0; width: 90px; height: 70px; }
</style>
</head>
<body>

  <section class="sheet card-front" aria-label="Business card front">
    <div class="brand"><span class="brand-mark"></span>PVTRN</div>
  </section>

  <section class="sheet card-back" aria-label="Business card back">
    <div class="brand"><span class="brand-mark"></span>PVTRN</div>
    <div class="name-strip">
      <div class="person">Morgan Feltwick</div>
      <div class="role">Director</div>
    </div>
    <ul class="contact-list">
      <li><span class="dot"></span>1200 Main Street</li>
      <li><span class="dot"></span>(555) 014-2280</li>
      <li><span class="dot"></span>www.pvtrn.org</li>
    </ul>
  </section>

  <section class="sheet notebook" aria-label="Notebook cover">
    <div class="spiral"><span></span><span></span><span></span><span></span><span></span><span></span><span></span><span></span><span></span><span></span><span></span><span></span><span></span><span></span><span></span><span></span><span></span><span></span></div>
    <div class="brand"><span class="brand-mark"></span>PVTRN</div>
  </section>

  <section class="sheet letterhead" aria-label="Letterhead">
    <aside class="side-band">
      <ul class="contact-list">
        <li>1200 Main Street</li>
        <li>Riverton, ST 00000</li>
        <li><span class="dot"></span>(555) 014-2280</li>
        <li><span class="dot"></span>(555) 014-2281</li>
        <li><span class="dot"></span>www.pvtrn.org</li>
      </ul>
      <div class="green-block"></div>
    </aside>
    <div class="brand"><span class="brand-mark"></span>PVTRN</div>
    <article class="letter">
      <div class="recipient">Jane Porter<br>Site Manager<br>88 Oak Avenue<br>Riverton, ST 00000</div>
      <p>Dear Member,</p>
      <p>Thank you for your continued support of our association. This year we expanded training programs, hosted regional meetings and welcomed many new firms committed to green building practices across the construction industry.</p>
      <p>Our members share a goal of safer sites, better standards and lasting work. We will soon publish updated guidance and invite you to take part in the review.</p>
      <p>Please contact our office with any questions. We look forward to working with you.</p>
      <p>Sincerely yours,</p>
      <p class="signature">Morgan Feltwick</p>
    </article>
  </section>

  <section class="sheet envelope" aria-label="Envelope">
    <div class="brand"><span class="brand-mark"></span>PVTRN</div>
    <div class="dark-panel">
      <ul class="contact-list">
        <li>PVTRN</li>
        <li>1200 Main Street</li>
        <li>Riverton, ST 00000</li>
        <li><span class="dot"></span>(555) 014-2280</li>
        <li><span class="dot"></span>www.pvtrn.org</li>
      </ul>
      <div class="green-block"></div>
    </div>
  </section>

</body>
</html>
```